HALT THE CLAIMS

I'm virtually ready to launch my site, but I have a number of edits and modifications that need to be implemented. More importantly, I'm always looking to improve my site, particularly now that I am making my proverbial "FIRST IMPRESSION." Thus, I'm willing to see if there is someone who can add creativity and perhaps improve what I already have, particularly on the All Important Front Page.

```html
<!DOCTYPE html>
<html lang="en">
<head>
<meta charset="utf-8">
<title>Halt The Claims</title>
<link href="https://fonts.googleapis.com/css2?family=Noto+Serif:wght@400;600;700;800&display=swap" rel="stylesheet">
<style>
:root{
  --navy:#0f2b5e;
  --navy-deep:#0d2550;
  --red:#a30d1b;
  --white:#ffffff;
  --ink:#333a45;
  --muted:#4a4f58;
  --faq-bg:#eceff3;
  --footer:#262626;
  --line:#444;
}
*{box-sizing:border-box;margin:0;padding:0}
html,body{width:1200px;height:2813px;overflow:hidden}
body{position:relative;font-family:"Noto Serif",serif;color:var(--ink);background:var(--white)}
.abs{position:absolute}
a{color:inherit;text-decoration:none}

/* top bar */
.topbar{left:0;top:0;width:1200px;height:46px}
.topbar > svg{position:absolute;left:0;top:0}
.topinfo{color:var(--white);font-size:12px;display:flex;align-items:center;gap:10px;line-height:17px}
.topinfo svg{flex:none}

.brand{left:103px;top:16px;width:134px;height:134px;border-radius:50%;background:var(--white);border:5px solid var(--navy);display:flex;align-items:center;justify-content:center;text-align:center;z-index:5}
.brand span{font-size:16px;font-weight:700;color:var(--red);line-height:19px;width:90px}

.nav{top:72px;left:467px;display:flex;gap:32px;font-size:12px;color:#333}
.social{top:65px;width:34px;height:34px;border:1.5px solid #333;border-radius:50%}
.btn{display:flex;align-items:center;justify-content:center;font-size:14px;color:var(--white)}
.btn-red{background:var(--red)}
.btn-ghost{border:1.5px solid var(--white)}

/* hero */
.hero{left:0;top:115px;width:1200px;height:560px;background:linear-gradient(100deg,#12305f 0%,#1a3a6e 55%,#173566 100%)}
.hero-photo{left:693px;top:87px;width:280px;height:473px;border-radius:140px 140px 0 0;background:linear-gradient(180deg,#6d7890 0%,#2a3f78 45%,#1e3470 100%)}
.hero h1{left:103px;top:183px;width:520px;font-size:44px;line-height:52px;font-weight:800;color:var(--white);letter-spacing:.3px}
.hero p{left:104px;top:294px;width:400px;font-size:12.5px;line-height:22.5px;color:var(--white)}

/* about */
.about-frame{left:100px;top:739px;width:110px;height:109px;border:2px solid var(--navy)}
.about-photo{left:118px;top:755px;width:424px;height:426px;background:linear-gradient(160deg,#3a3a34 0%,#5b5448 45%,#2e2a26 100%)}
.h2{font-size:30px;font-weight:800;color:var(--navy);letter-spacing:.3px}
.about{left:600px;top:773px;width:492px;display:flex;flex-direction:column;align-items:flex-start}
.about-text{margin-top:10px;font-size:13px;line-height:22.4px;color:var(--muted);letter-spacing:-.1px}
.about-text p+p{margin-top:8px}
.about .btn{margin-top:14px;width:104px;height:37px}

/* services */
.services{left:0;top:1262px;width:1200px;height:722px;background:linear-gradient(180deg,#173566 0%,#1b3a6c 50%,#16315f 100%)}
.services-intro{left:61px;top:130px;width:380px;color:var(--white)}
.services-intro h2{font-size:29px;font-weight:700}
.services-intro p{font-size:12.5px;line-height:20px;margin-top:10px}
.card{width:257px;height:242px;border:1.5px solid var(--white);color:var(--white);text-align:center;padding:18px 6px 0;display:flex;flex-direction:column;align-items:center}
.card svg{display:block;flex:none}
.card h3{font-size:15.5px;font-weight:600;margin-top:12px;white-space:nowrap;letter-spacing:-.2px;line-height:22px}
.card p{font-size:9.6px;line-height:16.5px;margin-top:5px;height:66px;overflow:hidden}
.card a{display:block;font-size:14px;font-weight:600;text-decoration:underline;margin-top:8px}
.card.active{background:var(--white);color:var(--navy)}
.card.active p{color:#4e5a70}

/* faq */
.faq-title{left:0;top:2056px;width:1200px;text-align:center}
.faq-item{width:459px;background:var(--faq-bg);border-radius:4px;padding:0 90px 0 18px;display:flex;align-items:center;font-size:17px;font-weight:600;color:var(--navy);line-height:25px}
.faq-item .chev{position:absolute;right:20px;top:50%;margin-top:-18px;width:36px;height:36px;border-radius:50%;background:var(--navy)}
.faq-item .chev::after{content:"";position:absolute;left:14px;top:12px;width:7px;height:7px;border-right:2px solid #fff;border-bottom:2px solid #fff;transform:rotate(45deg)}
.faq-open{background:var(--white);box-shadow:0 2px 10px rgba(0,0,0,.12);display:block;padding:20px 80px 0 18px}
.faq-open .chev{top:20px;margin-top:0}
.faq-open .chev::after{top:16px;transform:rotate(-135deg)}
.faq-open p{font-size:11.5px;line-height:19px;color:#555;font-weight:400;margin-top:12px;padding-left:6px}

/* footer */
.footer{left:0;top:2493px;width:1200px;height:320px;background:var(--footer);color:var(--white)}
.f-logo{left:105px;top:72px;width:114px;height:114px;border-radius:50%;background:var(--white);border:5px solid var(--navy);display:flex;align-items:center;justify-content:center;text-align:center}
.f-logo span{font-size:14px;font-weight:700;color:var(--red);line-height:17px;width:76px}
.footer h4{font-size:18px;font-weight:600}
.f-list{font-size:13px;line-height:23px}
.f-contact{font-size:14px;line-height:22px}
.field{width:177px;height:37px;border:1.5px solid var(--white);font-size:12px;padding:0 8px;display:flex;align-items:center}
.f-rule{left:105px;top:250px;width:990px;height:1px;background:var(--line)}
.copy{left:0;top:278px;width:1200px;text-align:center;font-size:12px}
</style>
</head>
<body>

<!-- top bar -->
<div class="abs topbar">
  <svg width="1200" height="46"><polygon points="248,0 1200,0 1200,46 270,46" fill="var(--navy-deep)"/></svg>
  <div class="abs topinfo" style="left:357px;top:7px;width:280px">
    <svg width="14" height="18" viewBox="0 0 14 18"><path d="M7 0a7 7 0 0 0-7 7c0 5 7 11 7 11s7-6 7-11a7 7 0 0 0-7-7zm0 10a3 3 0 1 1 0-6 3 3 0 0 1 0 6z" fill="#fff"/></svg>
    <span>4820 Canyon Ridge Rd., Suite 210 Mesa,<br>Arizona 85201</span>
  </div>
  <div class="abs topinfo" style="left:692px;top:15px">
    <svg width="16" height="16" viewBox="0 0 16 16"><path d="M3 1l3 3-2 2c1 2 4 5 6 6l2-2 3 3-2 2C7 15 1 9 1 3z" fill="#fff"/></svg>
    <span>480.555.0142 / 800.555.0178</span>
  </div>
  <div class="abs topinfo" style="left:935px;top:15px">
    <svg width="20" height="15" viewBox="0 0 20 15"><rect width="20" height="15" rx="1" fill="#fff"/><path d="M1 1l9 7 9-7" stroke="var(--navy-deep)" stroke-width="1.5" fill="none"/></svg>
    <span>info@haltclaims.example</span>
  </div>
</div>

<div class="abs brand"><span>Halt The Claims</span></div>

<nav class="abs nav"><a>Home</a><a>About Us</a><a>Services</a><a>Faq</a></nav>
<div class="abs social" style="left:735px"></div>
<div class="abs social" style="left:781px"></div>
<div class="abs social" style="left:826px"></div>
<a class="abs btn btn-red" style="left:895px;top:62px;width:201px;height:37px">Schedule Free Consultation</a>

<!-- hero -->
<section class="abs hero">
  <div class="abs hero-photo" role="img" aria-label="Portrait of a smiling attorney in a navy suit with arms crossed, office in background"></div>
  <h1 class="abs">WELCOME TO HALT THE CLAIMS</h1>
  <p class="abs">Business Owners: Halt The Claims (Htc) Is An Extremely Affordable Legal Service Plan (As Little As $8.00 Per Month) That Insulates Business Owners From Unwarranted Legal Claims And Expensive Lawsuits.</p>
  <a class="abs btn btn-red" style="left:106px;top:398px;width:120px;height:36px">Learn More</a>
  <a class="abs btn btn-ghost" style="left:247px;top:398px;width:200px;height:36px">Schedule Free Consultation</a>
</section>

<!-- about -->
<div class="abs about-frame"></div>
<div class="abs about-photo" role="img" aria-label="Attorney writing notes at a desk in front of a bookshelf"></div>
<div class="abs about">
  <h2 class="h2">ABOUT US</h2>
  <div class="about-text">
    <p>Htc Is A Group Of Attorney And Legal Assistants With Many Years Of Experience In Litigation, Who Are Devoted To Preventing Legal Claims And Costly Lawsuits Through A Variety Of Free And Very Affordable Services Described Below.Our Unique Service Plan Makes It Possible For Us To Halt The Claims.</p>
    <p>A homebuilding company was sued by a former employee who claimed to have been promised a more favorable sales area, which claim was disputed by the homebuilder. There was no evidence that such a promise had been made, other than the plaintiff's oral testimony. The company had the case dismissed, but spent $10,000 defending the case.And even though it was awarded its attorney's fees, the plaintiff proved uncollectible. Had the company been an HTC member, the case likely would never have been filed.</p>
  </div>
  <a class="btn btn-red">Read More</a>
</div>

<!-- services -->
<section class="abs services">
  <div class="abs services-intro">
    <h2>Our Services</h2>
    <p>The price for a membership is a ridiculously low $9.95 PER WEEK. We believe that this fee is very affordable. So what is it? Membership includes the following:</p>
  </div>

  <div class="abs card" style="left:608px;top:92px">
    <svg width="72" height="68" viewBox="0 0 72 68" fill="none" stroke="#fff" stroke-width="4"><rect x="10" y="2" width="22" height="16" rx="2"/><rect x="40" y="2" width="22" height="16" rx="2"/><circle cx="20" cy="32" r="6"/><circle cx="52" cy="32" r="6"/><path d="M6 66V50a10 10 0 0 1 20 0M46 50a10 10 0 0 1 20 0v16M18 48h36"/></svg>
    <h3>Free Initial Consultation</h3>
    <p>As a prospective Halt The Claims ("HTC") member, we urge you to schedule an initial consultation with us – at no charge – where we will go over each of the services in detail,</p>
    <a>Read More</a>
  </div>
  <div class="abs card" style="left:882px;top:92px">
    <svg width="72" height="68" viewBox="0 0 72 68" fill="none" stroke="#fff" stroke-width="4"><rect x="16" y="2" width="40" height="46" rx="3"/><path d="M36 12l10 4v8c0 6-5 10-10 12-5-2-10-6-10-12v-8z"/><path d="M4 54c10-8 20-4 30 0h20l14-8"/></svg>
    <h3>Proprietary Contract Language</h3>
    <p>HTC members are entitled to incorporate exclusive proprietary contract language in their contracts, work orders, and other written agreements in their business, that MINIMIZES EXPOSURE to legal</p>
    <a>Read More</a>
  </div>
  <div class="abs card" style="left:61px;top:353px">
    <svg width="80" height="68" viewBox="0 0 80 68" fill="none" stroke="#fff" stroke-width="4"><circle cx="18" cy="10" r="6"/><circle cx="62" cy="10" r="6"/><rect x="32" y="2" width="16" height="12" rx="2"/><path d="M6 34h68M10 34v-8h60v8"/><circle cx="14" cy="48" r="5"/><circle cx="40" cy="48" r="5"/><circle cx="66" cy="48" r="5"/><path d="M4 66a10 10 0 0 1 20 0M30 66a10 10 0 0 1 20 0M56 66a10 10 0 0 1 20 0"/></svg>
    <h3>Free Consultation</h3>
    <p>HTC members can call their local HTC Attorney any time, and be given a 30 minute consultation, free of charge, once per month. The value of this cannot be overstated and easily pays for the</p>
    <a>Read More</a>
  </div>
  <div class="abs card" style="left:336px;top:353px">
    <svg width="60" height="68" viewBox="0 0 60 68" fill="#fff"><circle cx="30" cy="16" r="14"/><path d="M4 68V46a14 14 0 0 1 14-14h24a14 14 0 0 1 14 14v22z"/></svg>
    <h3>Free Attorney Letters</h3>
    <p>In addition to free monthly consultations, HTC members can have their local HTC Attorney send out a letter regarding their business, once per month, at no charge.</p>
    <a>Read More</a>
  </div>
  <div class="abs card active" style="left:608px;top:353px">
    <svg width="96" height="68" viewBox="0 0 96 68" fill="none" stroke="var(--navy)" stroke-width="5"><circle cx="48" cy="8" r="6"/><rect x="38" y="20" width="20" height="22"/><circle cx="14" cy="20" r="6"/><circle cx="82" cy="20" r="6"/><path d="M6 34c0 14 8 20 18 20v12M90 34c0 14-8 20-18 20v12M30 66V44M66 66V44"/></svg>
    <h3>Litigation Discounts</h3>
    <p>HTC members who use the Proprietary Contract Language described above are given considerable discounts, including flat fee discounts, in the event of defensive litigation.</p>
    <a>Read More</a>
  </div>
  <div class="abs card" style="left:882px;top:353px">
    <svg width="76" height="72" viewBox="0 0 76 72" fill="none" stroke="#fff" stroke-width="4"><rect x="4" y="2" width="14" height="20"/><rect x="31" y="2" width="14" height="20"/><rect x="58" y="2" width="14" height="20"/><path d="M11 22v8h54v-8M38 22v14"/><ellipse cx="38" cy="44" rx="16" ry="5"/><path d="M22 44v20c0 3 7 5 16 5s16-2 16-5V44M22 54c0 3 7 5 16 5s16-2 16-5"/></svg>
    <h3>Collections</h3>
    <p>HTC members can have their HTC Attorney pursue collection claims on a contingency fee basis, provided the claim is based on a contract.</p>
    <a>Read More</a>
  </div>
</section>

<!-- faq -->
<h2 class="abs h2 faq-title">FREQUENTLY ASKED QUESTIONS</h2>
<div class="abs faq-item" style="left:132px;top:2125px;height:76px">Why should I be concerned about legal claims?<span class="chev"></span></div>
<div class="abs faq-item" style="left:132px;top:2215px;height:75px">Provide more details about the value of HTC's contract language.<span class="chev"></span></div>
<div class="abs faq-item" style="left:132px;top:2306px;height:110px">If I'm a contractor, for example, how can an HTC membership minimize legal claims against my business?<span class="chev"></span></div>
<div class="abs faq-item" style="left:609px;top:2125px;height:76px">What does an HTC membership cost?<span class="chev"></span></div>
<div class="abs faq-item faq-open" style="left:609px;top:2215px;height:173px">Do you have a Referral Program?<span class="chev"></span>
  <p>Lorem ipsum dolor sit amet, consectetur adipiscing elit. Suspendisse varius enim in eros elementum tristique. Duis cursus, mi quis viverra ornare, eros dolor interdum nulla, ut commodo diam libero vitae erat. Aenean faucibus nibh et justo cursus id rutrum lorem imperdiet. Nunc ut sem vitae risus tristique posuere.</p>
</div>

<!-- footer -->
<footer class="abs footer">
  <div class="abs f-logo"><span>Halt The Claims</span></div>
  <h4 class="abs" style="left:283px;top:68px">Quick Links</h4>
  <div class="abs f-list" style="left:283px;top:102px">Home<br>About Us<br>Services<br>Faq<br>Contact Us</div>
  <div class="abs f-list" style="left:379px;top:102px">Faq<br>Contact Us<br>Terms Of Service<br>Privacy Policy</div>
  <h4 class="abs" style="left:521px;top:68px">Contact Details</h4>
  <div class="abs f-contact" style="left:521px;top:102px">4820 Canyon Ridge Rd.,<br>Suite 210, Mesa, Arizona 85201</div>
  <div class="abs f-contact" style="left:522px;top:157px">(480) 555-0193 / (800) 555-0121</div>
  <div class="abs f-contact" style="left:522px;top:190px">info@haltclaims.example</div>
  <h4 class="abs" style="left:772px;top:68px">Get In Touch</h4>
  <div class="abs field" style="left:773px;top:109px">Name</div>
  <div class="abs field" style="left:960px;top:109px">Email</div>
  <div class="abs field" style="left:773px;top:158px">Phone</div>
  <div class="abs btn btn-red" style="left:960px;top:158px;width:177px;height:37px;font-weight:700;font-size:13px">Submit</div>
  <div class="abs f-rule"></div>
  <div class="abs copy">©Copyrights 2023 Company Name | All Rights Reserved</div>
</footer>

</body>
</html>
```